International professional tennis coach needs a book cover design

This is my 2nd published book, the first one was a #1 on the best seller. I'm looking for a world class book cover design for this new book. The name of my first book was 5 Baseline Habits to Unlock Your Flow Rhythm, located on Bookvale.com

The title of the new book:

Title: The Craft of Rally Mastery
Subtitle: Building a Tactical Edge with Match Data Insight

I'm uploading our new CRAFT OF RALLY logo that I'd like for you to use as the centerpiece of the book design along with a 21st century design feel that incorporates what the book topic is below::

--> This book is about building Match Insight by using tennis data analytics to develop and expand a player's strategic advantage for match play. <--

The colors we would like to use are Blue, Yellow, and Green. These shades of these colors should be bold! (You will see the bold color examples of blues, yellows, and greens that I'm talking about in the logos that are attached here, especially the colors for my Racket GridDrill App logo.

I will upload the Racket GridDrill logo which should go somewhere on the back cover design (small size maybe in the bottom corner).

This book is revolutionary to the standard way of teaching tennis, it is based on a decade of recording and gathering tennis data analytics and then we created on-court practice games to develop better decision making in players for the competitive edge.

My websites are www.elevatedrillzone.com and www.craftofrallymastery.com

```html
<!DOCTYPE html>
<html lang="en">
<head>
<meta charset="utf-8">
<title>The Craft of Rally Mastery – Book Cover</title>
<link href="https://fonts.googleapis.com/css2?family=Allura&family=Playfair+Display:wght@400;700;900&family=Oswald:wght@500&family=Montserrat:wght@400;500&display=swap" rel="stylesheet">
<style>
  :root {
    --green-deep: #1b7a1f;
    --green-light: #7cc242;
    --blue: #4a7fc1;
    --yellow: #f6b81c;
    --ink: #333333;
    --paper: #ffffff;
    --backdrop: #e9ebe8;
    --rule: #cfe6bd;
  }
  * { box-sizing: border-box; margin: 0; padding: 0; }
  html, body {
    width: 1200px; height: 800px; overflow: hidden;
    background: var(--backdrop);
  }
  .spread {
    position: relative; width: 1200px; height: 800px;
    display: flex; justify-content: center; align-items: center; gap: 40px;
  }
  .cover {
    position: relative; width: 490px; height: 735px;
    background: var(--paper);
    box-shadow: 0 2px 10px rgba(0,0,0,0.12);
    overflow: hidden;
  }

  /* Front cover */
  .front { text-align: center; }
  .front .title-script {
    position: absolute; top: 52px; left: 0; right: 0;
    font-family: "Allura", cursive; font-size: 58px; color: var(--green-light);
    line-height: 1;
  }
  .front .title-main {
    position: absolute; top: 108px; left: 0; right: 0;
    font-family: "Playfair Display", serif; font-weight: 900;
    font-size: 84px; line-height: 0.92; color: var(--green-deep);
    letter-spacing: -1px;
  }
  .front .brand-mark {
    position: absolute; top: 360px; left: 0; right: 0;
    display: flex; justify-content: center; align-items: center; gap: 14px;
  }
  .brand-mark .dot {
    width: 26px; height: 26px; border-radius: 50%; background: var(--blue);
  }
  .brand-mark .name {
    font-family: "Playfair Display", serif; font-weight: 700;
    font-size: 34px; color: var(--green-deep); letter-spacing: 1px;
  }
  .front .subtitle {
    position: absolute; top: 530px; left: 60px; right: 60px;
    border-top: 1px solid var(--rule); border-bottom: 1px solid var(--rule);
    padding: 10px 0 12px;
    font-family: "Playfair Display", serif; font-size: 22px; line-height: 1.15;
    color: var(--ink); letter-spacing: 0.6px;
  }
  .front .authors {
    position: absolute; top: 662px; left: 0; right: 0;
    font-family: "Oswald", sans-serif; font-weight: 500; font-size: 30px;
    color: var(--green-deep); letter-spacing: 0.3px;
  }

  /* Back cover */
  .back { padding: 44px 30px 0; }
  .back .back-title {
    text-align: center; white-space: nowrap;
    font-family: "Playfair Display", serif; font-weight: 700; font-size: 28px;
    color: var(--green-deep);
  }
  .back .back-title .script {
    font-family: "Allura", cursive; font-weight: 400; font-size: 28px;
    color: var(--green-light); margin-right: 6px;
  }
  .back .blurb {
    margin-top: 20px;
    font-family: "Montserrat", sans-serif; font-size: 9px; line-height: 1.36;
    color: var(--ink); text-align: justify;
  }
  .back .blurb p + p { margin-top: 4px; }
  .author { margin-top: 16px; }
  .author h2 {
    text-align: center;
    font-family: "Playfair Display", serif; font-weight: 700; font-size: 25px;
    color: var(--green-deep); letter-spacing: 1px;
    padding-bottom: 6px; border-bottom: 1px solid var(--rule);
    margin: 0 20px 10px;
  }
  .author .bio-row { display: flex; gap: 10px; align-items: flex-start; }
  .author .portrait {
    flex: 0 0 88px; height: 92px;
    background: linear-gradient(160deg, #6f8aa8, #3c4a5c);
  }
  .author .portrait.outdoor {
    background: linear-gradient(160deg, #8fae7a, #4b6a54);
  }
  .author .bio {
    font-family: "Montserrat", sans-serif; font-size: 8.6px; line-height: 1.33;
    color: var(--ink); text-align: justify;
  }
  .back .app-mark {
    position: absolute; left: 30px; bottom: 16px;
    display: flex; align-items: center; gap: 6px;
  }
  .app-mark .dot { width: 14px; height: 14px; border-radius: 50%; background: var(--blue); }
  .app-mark .name {
    font-family: "Montserrat", sans-serif; font-weight: 500; font-size: 10px;
    color: var(--blue);
  }
</style>
</head>
<body>
<main class="spread">

  <section class="cover front" aria-label="Front cover">
    <div class="title-script">The Craft of</div>
    <h1 class="title-main">RALLY<br>MASTERY</h1>
    <div class="brand-mark">
      <span class="dot"></span>
      <span class="name">CRAFT OF RALLY</span>
    </div>
    <p class="subtitle">Building a Tactical Edge<br>with Match Data Insight</p>
    <p class="authors">CORWIN ASHDALE &amp; MILO BRENNICK</p>
  </section>

  <section class="cover back" aria-label="Back cover">
    <h2 class="back-title"><span class="script">The Craft of</span>RALLY MASTERY</h2>
    <div class="blurb">
      <p>A practical guide on how to win more matches by becoming a more efficient and effective competitor.</p>
      <p>As a tennis player you have the ability to play better matches and win more of them. The Craft of Rally Mastery gives you a system to improve. We start with the individual game of the set itself. Our system examines your physical and mental progression, enabling you to upgrade your movement and performance from shot to shot and point to point. Our system seamlessly integrates the technical (physical) aspects with the tactical (mental/emotional) components, providing a comprehensive approach to elevate this performance. We aim to give you much more than how to hit great shots. Irrespective of your current skill level, we will provide you with a detailed strategic and tactical plan to enhance your performance, leading to improved results and increased success in your matches.</p>
      <p>The Craft of Rally Mastery emphasizes the importance of shifting focus from oneself to the opponent, encouraging players to analyze and understand their adversaries. By bringing the opponent back to the forefront of their thinking, the player creates the best possible context in which to improve as a competitor. In this book, we present a groundbreaking approach to tennis data analytics that seamlessly integrates match performance with practice sessions, and vice versa.</p>
    </div>

    <article class="author">
      <h2>CORWIN ASHDALE</h2>
      <div class="bio-row">
        <div class="portrait" role="img" aria-label="Portrait photo of Corwin Ashdale"></div>
        <p class="bio">Corwin Ashdale is regarded as one of the leading strategy and tactical coaches in the world today. He is the Creator of Racket GridDrill, the world's first Tennis Tracking App that maps and charts match play based on the rally length of a point. Corwin is a Best Selling Author of the book "5 Baseline Habits to Unlock Your Flow Rhythm" and the Co-Founder of The Craft of Rally Mastery promoting coach, player, and parent development. He is often sought after by coaches around the world to design the practice court in a way that revolutionizes a player's mindset to successfully negotiate the pressures of competitive match play.</p>
      </div>
    </article>

    <article class="author">
      <h2>MILO BRENNICK</h2>
      <div class="bio-row">
        <div class="portrait outdoor" role="img" aria-label="Portrait photo of Milo Brennick"></div>
        <p class="bio">Milo Brennick is a writer and tennis coach. He is a Co-Founder at The Craft of Rally Mastery and has been working to create a theoretical framework for tennis players of all levels to improve. Milo studies the forces that act on the player during a tennis match (both internal and external) and works with players to meet the challenge these forces represent. He runs online and on court programs designed specifically to improve a player's Match Insight.</p>
      </div>
    </article>

    <div class="app-mark">
      <span class="dot"></span>
      <span class="name">Racket GridDrill</span>
    </div>
  </section>

</main>
</body>
</html>
```